Poster for Kirtan Music Event

Design (3) 24" x 36" Posters

I have provided a sample a friend did in Australia: ( Picture No. 4 )

Use all the text on sample poster except the replacement changes below.

Replace with the following text as this is for different location:
Replacement Text:

Every Friday Night 7:00pm-8:30pm
Kealoha Pilates & Movement Studio
947 Hollister Rd Paia

Free Kirtan Experience! or Free Event
Mohan Priya Sevi & Companions

Optional Text:

A evening of music, singing of spiritual mantras, and refreshments

Bring flowers, musical instruments, friends, or just come with an open heart.

Meditate on transcendental sounds that provide rest for the mind & heart"

An evening of music & singing of sacred mantra's

```html
<!DOCTYPE html>
<html lang="en">
<head>
<meta charset="utf-8">
<title>Kirtan Experience – Every Friday Night</title>
<link rel="stylesheet" href="https://fonts.googleapis.com/css2?family=Poiret+One&family=Dosis:wght@500;600;700&family=Oswald:wght@400;500&display=swap">
<style>
  :root {
    --plum-deep: #3a0f3f;
    --plum: #6b1f6e;
    --magenta: #a83a9a;
    --orchid: #d27ac6;
    --blush: #f7d6ef;
    --peach: #ffc98a;
    --cream: #fff4ea;
    --ornament: #f3b9e6;
  }
  html, body {
    margin: 0;
    padding: 0;
    width: 802px;
    height: 1200px;
    overflow: hidden;
    background: var(--plum-deep);
  }
  .poster {
    position: relative;
    width: 802px;
    height: 1200px;
    overflow: hidden;
    background:
      radial-gradient(circle at 50% 78%, rgba(210,122,198,.55) 0, rgba(168,58,154,.35) 22%, transparent 48%),
      radial-gradient(circle at 50% 36%, var(--magenta) 0, var(--plum) 45%, var(--plum-deep) 100%);
    font-family: "Dosis", sans-serif;
    color: var(--cream);
  }
  .mandala-backdrop {
    position: absolute;
    left: -120px;
    top: 560px;
    width: 1042px;
    height: 700px;
    background: radial-gradient(ellipse at 50% 45%, rgba(247,214,239,.18) 0, rgba(210,122,198,.12) 30%, transparent 62%);
  }
  .musicians-photo {
    position: absolute;
    left: 0;
    top: 120px;
    width: 802px;
    height: 480px;
    background:
      radial-gradient(ellipse at 35% 45%, rgba(240,200,180,.55) 0, rgba(190,110,150,.35) 30%, transparent 60%),
      radial-gradient(ellipse at 70% 40%, rgba(230,180,190,.45) 0, rgba(170,80,140,.25) 28%, transparent 55%),
      linear-gradient(180deg, rgba(107,31,110,.2), rgba(168,58,154,.35) 70%, transparent);
  }
  .rule {
    position: absolute;
    left: 100px;
    width: 602px;
    height: 0;
    border-top: 2px solid var(--ornament);
  }
  .rule-top { top: 38px; }
  .rule-bottom { top: 1158px; }
  .rule::after {
    content: "";
    position: absolute;
    left: 293px;
    top: -9px;
    width: 14px;
    height: 14px;
    background: var(--ornament);
    transform: rotate(45deg);
  }
  .bubble {
    position: absolute;
    margin: 0;
    width: 200px;
    height: 200px;
    border-radius: 50%;
    border: 3px dotted var(--blush);
    background: rgba(58,15,63,.55);
    box-sizing: border-box;
    display: flex;
    align-items: center;
    justify-content: center;
    text-align: center;
    padding: 26px;
    font-weight: 600;
    font-size: 19px;
    line-height: 1.2;
    color: var(--blush);
  }
  .bubble-invite { left: 598px; top: 58px; }
  .bubble-evening { left: 20px; top: 398px; background: rgba(58,15,63,.35); }
  .title {
    position: absolute;
    left: 0;
    top: 610px;
    width: 802px;
    margin: 0;
    text-align: center;
    white-space: nowrap;
    font-family: "Poiret One", sans-serif;
    font-weight: 400;
    font-size: 78px;
    letter-spacing: 2px;
    line-height: 1;
    transform: scaleY(1.4);
    transform-origin: top center;
    background: linear-gradient(180deg, #ffffff 0%, var(--blush) 45%, var(--orchid) 100%);
    -webkit-background-clip: text;
    background-clip: text;
    color: transparent;
    -webkit-text-stroke: 1px #ffffff;
  }
  .details {
    position: absolute;
    left: 0;
    top: 772px;
    width: 802px;
    text-align: center;
  }
  .details p { margin: 0; }
  .free-event, .host {
    font-weight: 600;
    font-size: 21px;
    line-height: 26px;
    color: var(--cream);
  }
  .venue, .address {
    font-weight: 600;
    font-size: 24px;
    line-height: 34px;
    color: var(--cream);
  }
  .stars {
    font-weight: 700;
    font-size: 20px;
    letter-spacing: 10px;
    line-height: 26px;
    color: var(--cream);
  }
  .schedule {
    font-family: "Oswald", sans-serif;
    font-weight: 400;
    font-size: 44px;
    line-height: 64px;
    color: var(--peach);
    letter-spacing: 0.5px;
  }
</style>
</head>
<body>
  <main class="poster">
    <div class="mandala-backdrop" role="img" aria-label="Soft radiating mandala pattern in pink and violet"></div>
    <div class="musicians-photo" role="img" aria-label="Photograph of two kirtan musicians singing, one playing a harmonium, bathed in purple light"></div>

    <div class="rule rule-top"></div>

    <p class="bubble bubble-invite">Join us in the singing of transcendental sounds that provide rest for the mind &amp; heart</p>
    <p class="bubble bubble-evening">An evening of music &amp; singing of sacred mantra's</p>

    <h1 class="title">KIRTAN EXPERIENCE</h1>

    <section class="details">
      <p class="free-event">Free Event!</p>
      <p class="host">Mohan Priya Sevi &amp; Companions</p>
      <p class="stars">***</p>
      <p class="schedule">Every Friday Night 7:00pm-8:30pm</p>
      <p class="stars">***</p>
      <p class="venue">Kealoha Pilates &amp; Movement Studio</p>
      <p class="address">947 Hollister Rd Paia</p>
      <p class="stars">***</p>
    </section>

    <div class="rule rule-bottom"></div>
  </main>
</body>
</html>
```